Weightloss company needs Business Card

We want a business card that is clean and professional, yet portrays that we are a friendly, innovative, and versatile program designed to fit the needs of our clients.
I would like there to be 2 sides, one side having an appointment card, and the other side containing the logo and business information. There can be decorations on both sides. The logo is attached.

Target Market(s)

Men and women 40-60

Industry/Entity Type

Business

Contact Information for Business Card

Font styles to use
Sans Serif

Requirements
Must have
• The logo, space for business information
Nice to have
• The colors in the logo
Should not have
• No pictures of people or food

```html
<!DOCTYPE html>
<html lang="en">
<head>
<meta charset="utf-8">
<title>Renewal Path – Business Card</title>
<link rel="stylesheet" href="https://fonts.googleapis.com/css2?family=Source+Sans+3:ital,wght@0,400;0,600;0,700;1,400;1,700&display=swap">
<style>
  :root {
    --brand-red: #e2173d;
    --brand-cyan: #22b8e0;
    --ink: #4a4a4a;
    --muted: #5e5e5e;
    --rule: #b9b9b9;
    --card: #f3f3f3;
    --backdrop: #e4e5e6;
  }
  * { box-sizing: border-box; margin: 0; padding: 0; }
  html, body {
    width: 1105px; height: 1200px; overflow: hidden;
    background: var(--backdrop);
    font-family: "Source Sans 3", sans-serif;
  }
  .card {
    position: absolute; left: 182px;
    width: 747px; height: 427px;
    background: var(--card);
    overflow: hidden;
  }
  .card--front { top: 119px; }
  .card--back { top: 637px; }

  /* Front */
  .brand {
    position: absolute; left: 72px; top: 196px;
    display: flex; align-items: center; gap: 12px;
  }
  .brand__dot { width: 22px; height: 22px; border-radius: 50%; background: var(--brand-red); }
  .brand__name { font-size: 40px; font-weight: 700; color: var(--brand-red); line-height: 1; }
  .divider {
    position: absolute; left: 395px; top: 81px;
    width: 1px; height: 242px; background: var(--rule);
  }
  .contact { position: absolute; left: 433px; top: 78px; color: var(--ink); }
  .contact__name { font-size: 29px; font-weight: 600; color: var(--brand-red); line-height: 1.1; }
  .contact__role { font-size: 20px; color: var(--brand-cyan); line-height: 1.2; margin-top: 2px; }
  .contact__address { margin-top: 12px; font-size: 19px; line-height: 28px; }
  .contact__list { list-style: none; margin-top: 4px; font-size: 19px; }
  .contact__list li { display: flex; align-items: center; height: 29px; gap: 12px; }
  .contact__list svg { width: 18px; height: 18px; fill: var(--brand-red); flex: none; }
  .band { position: absolute; left: 0; bottom: 0; width: 100%; height: 40px; }
  .band svg { display: block; }
  .band__web {
    position: absolute; right: 38px; bottom: 7px;
    color: #fff; font-size: 20px; font-weight: 700; font-style: italic; letter-spacing: 1px;
  }

  /* Back */
  .appt__title {
    position: absolute; top: 36px; width: 100%; text-align: center;
    font-size: 29px; font-weight: 600; color: var(--brand-red);
  }
  .field {
    position: absolute; display: flex; align-items: baseline;
    font-size: 20px; color: var(--brand-red);
  }
  .field__line { flex: 1; border-bottom: 2px dotted #8a8a8a; margin-left: 6px; height: 1px; transform: translateY(-3px); }
  .field__suffix { font-size: 16px; margin-left: 4px; }
  .field--name { left: 41px; right: 55px; top: 106px; }
  .field--date { left: 38px; width: 355px; top: 157px; }
  .field--time { left: 419px; right: 55px; top: 157px; }
  .field--note { left: 41px; right: 55px; top: 264px; }
  .field--note2 { left: 44px; right: 55px; top: 302px; }
  .days {
    position: absolute; left: 43px; right: 60px; top: 218px;
    display: flex; justify-content: space-between; list-style: none;
    font-size: 19px; color: var(--brand-red);
  }
  .days li { display: flex; align-items: center; gap: 8px; }
  .days li::after {
    content: ""; width: 22px; height: 18px; border: 1.5px solid #666; background: #fff;
  }
  .appt__policy {
    position: absolute; top: 355px; width: 100%; text-align: center;
    font-size: 15.5px; font-style: italic; color: var(--muted); line-height: 22px;
  }
</style>
</head>
<body>

<section class="card card--front">
  <div class="brand">
    <span class="brand__dot"></span>
    <span class="brand__name">Renewal Path</span>
  </div>
  <div class="divider"></div>
  <div class="contact">
    <p class="contact__name">DANIEL HART</p>
    <p class="contact__role">CEO/FOUNDER</p>
    <p class="contact__address">4120 Juniper Court<br>Fairview, Oregon 97024</p>
    <ul class="contact__list">
      <li><svg viewBox="0 0 24 24"><path d="M6.6 10.8a15.1 15.1 0 0 0 6.6 6.6l2.2-2.2c.3-.3.7-.4 1-.2 1.1.4 2.3.6 3.6.6.6 0 1 .4 1 1V20c0 .6-.4 1-1 1A17 17 0 0 1 3 4c0-.6.4-1 1-1h3.5c.6 0 1 .4 1 1 0 1.3.2 2.5.6 3.6.1.3 0 .7-.2 1z"/></svg>503 218 4471</li>
      <li><svg viewBox="0 0 24 24"><path d="M7 1h10a2 2 0 0 1 2 2v18a2 2 0 0 1-2 2H7a2 2 0 0 1-2-2V3a2 2 0 0 1 2-2zm0 3v14h10V4zm5 15.2a1.2 1.2 0 1 0 0 2.4 1.2 1.2 0 0 0 0-2.4z"/></svg>503 762 1089</li>
      <li><svg viewBox="0 0 24 24"><path d="M6 2h10l2 2v5h2a2 2 0 0 1 2 2v9a2 2 0 0 1-2 2H4a2 2 0 0 1-2-2v-9a2 2 0 0 1 2-2h2zm2 2v5h8V5zM5 14v2h14v-2zm0 4v1h14v-1z"/></svg>503 415 6320</li>
      <li><svg viewBox="0 0 24 24"><path d="M2 5h20v14H2zm2 2v.5l8 5 8-5V7zm0 2.8V17h16V9.8l-8 5z"/></svg>hello@renewalpath.com</li>
    </ul>
  </div>
  <div class="band">
    <svg width="747" height="40" viewBox="0 0 747 40">
      <polygon points="0,15 452,15 437,40 0,40" fill="var(--brand-cyan)"/>
      <polygon points="452,15 460,15 445,40 437,40" fill="#ffffff"/>
      <polygon points="476,0 747,0 747,40 438,40" fill="var(--brand-red)"/>
    </svg>
    <span class="band__web">www.renewalpath.com</span>
  </div>
</section>

<section class="card card--back">
  <h1 class="appt__title">Next Appointment</h1>
  <div class="field field--name">Name :<span class="field__line"></span></div>
  <div class="field field--date">Date :<span class="field__line"></span></div>
  <div class="field field--time">Time :<span class="field__line"></span><span class="field__suffix">AM/PM</span></div>
  <ul class="days">
    <li>Sun</li><li>Mon</li><li>Tue</li><li>Wed</li><li>Thu</li><li>Fri</li><li>Sat</li>
  </ul>
  <div class="field field--note">Note :<span class="field__line"></span></div>
  <div class="field field--note2"><span class="field__line"></span></div>
  <p class="appt__policy">Please give me 24 hours notice if you are unable to keep your appointment or<br>a cancellation fee may be charged.</p>
</section>

</body>
</html>
```